Business card for denture clinic Veltrimora

We need a new business card with our new logo. We are a denture clinic in New Zealand with our target market being 45+ years old. We would need a space on the back to write our patients next appointment on. We would space for only one appointment rather than a list. We will attach a photo showing an example of this. But of course, we would like to see your twist on this. We want it to be bold and easy to read and a good mixture of professional but modern. We have attached our logo to be used on the card.

Target Market(s)

People aged 45+ needing dentures

Industry/Entity Type

Dental

Contact Information for Business Card

We want our logo on the front and the space to write an appointment on the back. I've attached an example our our old business card showing this. We need to have the technicians details on the front.

Font styles to use
Sans Serif

Colors
0255a3
919191
fbfbfb

Requirements
Must have
• The following details:
• Liam Dorsett BDT, PGDipCDentTech Calverin
• Dental Prosthetist
• Phone numbers: 0800 47 3125
• 09 572 1394
• Email: liam@veltrimora.co.nz
• www.veltrimora.co.nz
• Address: 14 Marlow Crest Road
• Halbrook West
• Auckland 0793
Nice to have
• We would like our business cards to have more than just two colours as we want them to be more vibrant. We have uploaded an example of a business card we liked that showed this.

```html
<!DOCTYPE html>
<html lang="en">
<head>
<meta charset="utf-8">
<title>Veltrimora business card</title>
<link rel="stylesheet" href="https://fonts.googleapis.com/css2?family=Lato:ital,wght@0,400;0,700;0,900;1,400&display=swap">
<style>
  :root {
    --brand-blue: #0260a3;
    --brand-blue-deep: #0255a3;
    --ink: #1e1e1e;
    --card-white: #fbfbfb;
    --paper: #ffffff;
    --stage: #ececec;
    --watermark: rgba(255,255,255,0.09);
  }
  * { box-sizing: border-box; margin: 0; padding: 0; }
  html, body { width: 1200px; height: 586px; overflow: hidden; }
  body {
    background: var(--stage);
    font-family: "Lato", sans-serif;
    color: var(--ink);
    position: relative;
  }
  .card {
    position: absolute;
    top: 129px;
    width: 501px;
    height: 301px;
    overflow: hidden;
  }
  /* Back: appointment side */
  .card-back { left: 61px; background: var(--brand-blue); }
  .appointment-heading {
    height: 25px;
    background: var(--paper);
    color: var(--brand-blue);
    font-weight: 700;
    font-size: 13px;
    letter-spacing: 3.6px;
    text-align: center;
    line-height: 26px;
  }
  .field { position: absolute; top: 99px; width: 203px; }
  .field-date { left: 39px; }
  .field-time { left: 266px; }
  .field-label { color: var(--paper); font-size: 13px; display: block; height: 20px; }
  .field-box { height: 33px; background: var(--paper); border-radius: 4px; }
  .back-watermark {
    position: absolute;
    left: 0; right: 0; top: 212px;
    text-align: center;
    font-weight: 900;
    font-size: 40px;
    letter-spacing: 2px;
    color: var(--watermark);
    text-transform: uppercase;
  }
  /* Front: contact side */
  .card-front { left: 619px; background: var(--card-white); }
  .brand {
    position: absolute;
    left: 60px; top: 74px;
    width: 170px;
    text-align: center;
  }
  .brand-square {
    display: block;
    width: 34px; height: 34px;
    margin: 0 auto 6px;
    background: var(--brand-blue);
    border-radius: 3px;
  }
  .brand-name {
    font-weight: 700;
    font-size: 22px;
    letter-spacing: 1px;
    color: var(--brand-blue);
    text-transform: uppercase;
  }
  .hours {
    position: absolute;
    right: 279px; top: 166px;
    text-align: right;
    font-size: 12.5px;
    line-height: 21px;
  }
  .hours-title {
    color: var(--brand-blue);
    font-weight: 700;
    text-decoration: underline;
    text-underline-offset: 3px;
    margin-bottom: 6px;
  }
  .hours strong { font-weight: 700; }
  .divider {
    position: absolute;
    left: 260px; top: 64px;
    width: 2px; height: 170px;
    background: linear-gradient(to bottom, rgba(2,96,163,0), var(--brand-blue) 30%, var(--brand-blue) 70%, rgba(2,96,163,0));
  }
  .technician { position: absolute; left: 288px; top: 73px; }
  .technician-name { color: var(--brand-blue); font-weight: 700; font-size: 17px; }
  .technician-qual { font-style: italic; font-size: 11px; margin-top: 2px; }
  .technician-role { font-weight: 700; font-size: 11.5px; margin-top: 17px; }
  .contacts { position: absolute; left: 288px; top: 162px; list-style: none; }
  .contacts li {
    display: flex; align-items: center;
    height: 24px;
    font-size: 12.5px;
  }
  .contact-icon { width: 18px; height: 18px; margin-right: 7px; flex: none; }
  .address-band {
    position: absolute;
    left: 0; right: 0; bottom: 0;
    height: 25px;
    background: var(--brand-blue);
    color: var(--paper);
    font-weight: 700;
    font-size: 13px;
    text-align: center;
    line-height: 25px;
  }
</style>
</head>
<body>

<section class="card card-back" aria-label="Appointment side">
  <h2 class="appointment-heading">Your Next Appointment</h2>
  <div class="field field-date"><span class="field-label">Date:</span><div class="field-box"></div></div>
  <div class="field field-time"><span class="field-label">Time:</span><div class="field-box"></div></div>
  <div class="back-watermark" aria-hidden="true">Veltrimora</div>
</section>

<section class="card card-front" aria-label="Contact side">
  <div class="brand">
    <span class="brand-square"></span>
    <div class="brand-name">Veltrimora</div>
  </div>

  <div class="hours">
    <div class="hours-title">Opening Hours</div>
    <div><strong>Mon - Thurs:</strong> 9.00am - 5.00pm</div>
    <div><strong>Fri - Sat:</strong> 9.00am - 1.00pm</div>
  </div>

  <div class="divider"></div>

  <div class="technician">
    <div class="technician-name">Liam Dorsett BDT</div>
    <div class="technician-qual">PGDipCDentTech Calverin</div>
    <div class="technician-role">Dental Prosthetist</div>
  </div>

  <ul class="contacts">
    <li>
      <svg class="contact-icon" viewBox="0 0 18 18" aria-hidden="true"><circle cx="9" cy="9" r="9" fill="#0260a3"/><path d="M4.5 7.5c0-1.5 2-2.5 4.5-2.5s4.5 1 4.5 2.5l-1.6.4-.4-1.2H6.5l-.4 1.2zM6.3 8.3h5.4l1 4.2H5.3z" fill="#fff"/></svg>
      0800 47 3125
    </li>
    <li>
      <svg class="contact-icon" viewBox="0 0 18 18" aria-hidden="true"><circle cx="9" cy="9" r="9" fill="#0260a3"/><path d="M4.5 7.5c0-1.5 2-2.5 4.5-2.5s4.5 1 4.5 2.5l-1.6.4-.4-1.2H6.5l-.4 1.2zM6.3 8.3h5.4l1 4.2H5.3z" fill="#fff"/></svg>
      09 572 1394
    </li>
    <li>
      <svg class="contact-icon" viewBox="0 0 18 18" aria-hidden="true"><circle cx="9" cy="9" r="9" fill="#0260a3"/><rect x="4.5" y="5.8" width="9" height="6.4" fill="#fff"/><path d="M4.5 5.8 9 9.5l4.5-3.7" fill="none" stroke="#0260a3" stroke-width="0.9"/></svg>
      liam@veltrimora.co.nz
    </li>
  </ul>

  <div class="address-band">14 Marlow Crest Road, Halbrook West Auckland 0793</div>
</section>

</body>
</html>
```